Pepper & Palm Business Card FUN & EXCITING

Here is the Information for the Card:
Jaswinder Bains (Ravi)
E: RaviBains@postlark.com
C: (480) 555-0147
www.PepperPalmLV.com

We don't want traditional Indian cliche, We a playful bold and fun business card.

Files: https://files.cloudvessel.net/share/folders/7TqRmXpZ2vKa9LwBn4YcHd3JsEf6UoGi?usp=share_link

https://files.cloudvessel.net/share/folders/4MzXaQ8rTw2YbNcVk6PsLe5GhJdR3FoU?usp=share_link

Target Market(s)

Las Vegas Local Restaurant

Industry/Entity Type

Indian Restaurant

Contact Information for Business Card

Name, Email, Cell Phone, Company Logo

```html
<!DOCTYPE html>
<html lang="en">
<head>
<meta charset="utf-8">
<title>Pepper &amp; Palm — Business Card</title>
<link href="https://fonts.googleapis.com/css2?family=Montserrat:wght@400;600;800&display=swap" rel="stylesheet">
<style>
  :root {
    --backdrop: #2b2b2b;
    --card: #1e1e1e;
    --ink: #ffffff;
    --ink-muted: #e6e6e6;
    --accent: #f07f2a;
    --front-mark: #3c3c3c;
  }
  * { box-sizing: border-box; margin: 0; padding: 0; }
  html, body {
    width: 1200px; height: 1108px; overflow: hidden;
    background: var(--backdrop);
    font-family: "Montserrat", Arial, sans-serif;
  }
  .card {
    position: absolute; left: 258px; width: 696px;
    background: var(--card); border-radius: 18px;
  }
  .card--front { top: 128px; height: 425px; }
  .card--back { top: 596px; height: 438px; }

  .brand-name {
    position: absolute; left: 0; right: 0; text-align: center;
    font-weight: 800; letter-spacing: 0.5px; line-height: 1;
  }
  .card--front .brand-name { top: 185px; font-size: 52px; color: var(--front-mark); }
  .card--back .brand-name { top: 90px; font-size: 56px; color: var(--ink); }

  .owner {
    position: absolute; right: 344px; top: 287px; text-align: right;
  }
  .owner__name { font-weight: 600; font-size: 27px; color: var(--accent); line-height: 1.1; }
  .owner__role { font-size: 16px; color: var(--ink-muted); margin-top: 2px; }

  .divider {
    position: absolute; left: 362px; top: 270px; width: 2px; height: 84px;
    background: var(--accent);
  }

  .contacts { position: absolute; left: 376px; top: 274px; list-style: none; }
  .contacts li {
    display: flex; align-items: center; height: 26px;
    font-size: 16px; color: var(--ink);
  }
  .contacts svg { width: 14px; height: 14px; margin-right: 13px; fill: var(--accent); flex: none; }

  .address {
    position: absolute; left: 0; right: 0; top: 396px; text-align: center;
    font-size: 16px; color: var(--ink);
  }
</style>
</head>
<body>
  <section class="card card--front">
    <div class="brand-name">Pepper &amp; Palm</div>
  </section>

  <section class="card card--back">
    <div class="brand-name">Pepper &amp; Palm</div>

    <div class="owner">
      <div class="owner__name">Jaswinder Bains (Ravi)</div>
      <div class="owner__role">owner</div>
    </div>

    <div class="divider"></div>

    <ul class="contacts">
      <li>
        <svg viewBox="0 0 16 16" aria-hidden="true"><path d="M2 5c0-2 2-3 6-3s6 1 6 3v1h-3V5H5v1H2zM4 7h8l2 6H2zM8 8.5a2 2 0 1 0 0 4 2 2 0 0 0 0-4z"/></svg>
        (480) 555-0147
      </li>
      <li>
        <svg viewBox="0 0 16 16" aria-hidden="true"><path d="M1 3h14v1.5L8 9 1 4.5zM1 6.2l7 4.5 7-4.5V13H1z"/></svg>
        RaviBains@postlark.com
      </li>
      <li>
        <svg viewBox="0 0 16 16" aria-hidden="true"><path d="M8 1a7 7 0 1 0 0 14A7 7 0 0 0 8 1zm-1 2.2c-.6.8-1.8 1-2.3 2-.4.8.6 1.6 1.4 1.8.9.3 1 1.3.6 2.1-.3.7 0 1.7.6 2.2-.6.3-1.6.2-2.6-.6A5 5 0 0 1 7 3.2zm3.4 9c.4-.9 1.4-1.4 1.4-2.5 0-.8-1-1-1.7-1.2-.6-.2-.4-1-.9-1.3-.6-.3-1.3.1-1.5-.6-.1-.6.7-1 1.4-1.2a5 5 0 0 1 1.3 6.8z"/></svg>
        www.PepperPalmLV.com
      </li>
    </ul>

    <div class="address">418 Cedar Ridge Ave, #112 Marlow Falls, OH 43190</div>
  </section>
</body>
</html>
```